Business Card Design Project

Business Card
We are rebranding with a new logo
Industry/Entity Type
Business
Contact Information for Business Card
Dennis Morvale +61 487215963 dennis@quorv.com.au P.O. Box 872 Fernlow QLD 4309
Requirements
Must have
- Logo

```html
<!DOCTYPE html>
<html lang="en">
<head>
<meta charset="utf-8">
<title>Quorv International – Business Card</title>
<link rel="stylesheet" href="https://fonts.googleapis.com/css2?family=Lato:wght@400;700;900&display=swap">
<style>
  :root {
    --backdrop: #d6d4d5;
    --card-white: #ffffff;
    --brand-blue: #1ba3dc;
    --accent-blue: #7fcbef;
    --ink: #1c1c1c;
    --on-blue: #ffffff;
  }
  * { margin: 0; padding: 0; box-sizing: border-box; }
  html, body {
    width: 1200px; height: 1000px; overflow: hidden;
    background: var(--backdrop);
    font-family: "Lato", Arial, sans-serif;
  }
  .canvas { position: relative; width: 1200px; height: 1000px; }
  .business-card {
    position: absolute; left: 202px; top: 272px;
    width: 796px; height: 455px;
    background: var(--card-white);
    box-shadow: 0 6px 18px rgba(0,0,0,.25);
    overflow: hidden;
  }
  .card-panel { position: absolute; inset: 0; }
  .brand-mark {
    position: absolute; left: 80px; top: 178px;
    width: 330px;
    display: flex; align-items: center; gap: 14px;
  }
  .brand-mark__dot {
    width: 22px; height: 22px; border-radius: 50%;
    background: var(--brand-blue); flex: none;
  }
  .brand-mark__name {
    font-weight: 900; font-size: 24px; color: var(--ink);
    letter-spacing: 2px; line-height: 1.25;
  }
  .holder {
    position: absolute; left: 468px; top: 46px;
    display: flex; align-items: center; gap: 14px;
    color: var(--on-blue);
  }
  .holder__name { font-size: 31px; letter-spacing: 1px; font-weight: 400; }
  .holder__name strong { font-weight: 900; }
  .contact-list { position: absolute; left: 512px; top: 156px; list-style: none; }
  .contact-item {
    display: flex; align-items: flex-start; gap: 22px;
    color: var(--on-blue); font-weight: 700; font-size: 15.5px;
    letter-spacing: 1.2px; line-height: 33px;
    margin-bottom: 38px;
  }
  .contact-item svg { margin-top: 4px; flex: none; }
</style>
</head>
<body>
<main class="canvas">
  <article class="business-card">
    <svg class="card-panel" width="796" height="455" viewBox="0 0 796 455" aria-hidden="true">
      <polygon fill="var(--accent-blue)" points="436,0 796,0 796,455 436,455 436,226 418,208 436,190"/>
      <polygon fill="var(--brand-blue)" points="448,0 796,0 796,455 448,455 448,226 430,208 448,190"/>
    </svg>

    <div class="brand-mark">
      <span class="brand-mark__dot"></span>
      <span class="brand-mark__name">QUORV<br>INTERNATIONAL</span>
    </div>

    <div class="holder">
      <svg width="48" height="48" viewBox="0 0 48 48" aria-hidden="true" fill="none" stroke="#fff" stroke-width="2.5">
        <rect x="2" y="2" width="44" height="44" rx="10"/>
        <circle cx="24" cy="19" r="7"/>
        <path d="M11 37c2-7 7-10 13-10s11 3 13 10z"/>
      </svg>
      <h1 class="holder__name"><strong>Dennis</strong> Morvale</h1>
    </div>

    <ul class="contact-list">
      <li class="contact-item">
        <svg width="25" height="25" viewBox="0 0 25 25" fill="none" stroke="#fff" stroke-width="1.6" aria-hidden="true">
          <rect x="1" y="1" width="23" height="23" rx="5"/>
          <rect x="8" y="5" width="9" height="15" rx="1.5"/>
          <line x1="8" y1="17" x2="17" y2="17"/>
        </svg>
        <span>+61 487215963</span>
      </li>
      <li class="contact-item">
        <svg width="25" height="25" viewBox="0 0 25 25" fill="none" stroke="#fff" stroke-width="1.6" aria-hidden="true">
          <rect x="1" y="1" width="23" height="23" rx="5"/>
          <rect x="6" y="7" width="13" height="11"/>
          <path d="M6 7l13 11M19 7L6 18"/>
        </svg>
        <span>dennis@quorv.com.au</span>
      </li>
      <li class="contact-item">
        <svg width="25" height="25" viewBox="0 0 25 25" fill="none" stroke="#fff" stroke-width="1.6" aria-hidden="true">
          <rect x="1" y="1" width="23" height="23" rx="5"/>
          <path d="M12.5 19.5s-5-5-5-8.5a5 5 0 0 1 10 0c0 3.5-5 8.5-5 8.5z"/>
          <circle cx="12.5" cy="11" r="1.4" fill="#fff"/>
        </svg>
        <span>P.O. Box 872<br>Fernlow QLD 4309</span>
      </li>
    </ul>
  </article>
</main>
</body>
</html>
```